The Plate Compass

Cutting Through the Noise to What Actually Works.

Nutrition book

Target Market(s)

People looking to be or get healthy and eat right.

```html
<!DOCTYPE html>
<html lang="en">
<head>
<meta charset="utf-8">
<title>The Plate Compass</title>
<link href="https://fonts.googleapis.com/css2?family=Poppins:ital,wght@0,600;0,700;0,800;1,500&display=swap" rel="stylesheet">
<style>
  :root{
    --ink-teal:#2f5560;
    --title-orange:#ee7552;
    --title-green:#3f7150;
    --subtitle:#3a3a3a;
    --paper:#ffffff;
    --apex:#dd5a32;
    --apex-dark:#c9482a;
    --calories:#e0562e;
    --calories-dark:#c94826;
    --protein:#f4a466;
    --protein-dark:#e38e50;
    --quality:#efb6a6;
    --quality-dark:#e2a090;
    --timing:#9fae78;
    --timing-dark:#889a62;
    --supps:#76996c;
    --supps-dark:#5f8458;
    --noise:#2c5a4c;
    --noise-dark:#1d4238;
    --band:rgba(40,60,45,.55);
  }
  *{margin:0;padding:0;box-sizing:border-box}
  html,body{width:800px;height:1200px;overflow:hidden;background:var(--paper)}
  .cover{position:relative;width:800px;height:1200px;overflow:hidden;background:var(--paper);font-family:'Poppins',sans-serif}
  .scene{position:absolute;inset:0;width:800px;height:1200px}
  .title{position:absolute;left:0;width:800px;text-align:center;font-weight:700;line-height:1;letter-spacing:1px}
  .title-the{top:34px;font-size:112px;color:var(--ink-teal);font-weight:800}
  .title-plate{top:146px;font-size:92px;color:var(--title-orange)}
  .title-compass{top:242px;font-size:92px;color:var(--title-green)}
  .subtitle{position:absolute;top:340px;left:0;width:800px;text-align:center;font-style:italic;font-weight:500;font-size:35px;line-height:50px;color:var(--subtitle)}
  .tier-label{font-family:'Poppins',sans-serif;font-weight:700;font-size:25px;fill:#fff;filter:drop-shadow(1px 2px 1px rgba(0,0,0,.45))}
  .tier-icon{fill:#fff;stroke:#fff;filter:drop-shadow(1px 2px 1px rgba(0,0,0,.35))}
  .author-band{position:absolute;left:150px;top:1124px;width:500px;height:52px;background:linear-gradient(90deg,rgba(40,60,45,0),var(--band) 20%,var(--band) 80%,rgba(40,60,45,0));display:flex;align-items:center;justify-content:center}
  .author-name{color:#fff;font-weight:700;font-size:27px;letter-spacing:.5px;text-shadow:1px 2px 2px rgba(0,0,0,.35)}
</style>
</head>
<body>
<div class="cover">
  <svg class="scene" viewBox="0 0 900 1350" xmlns="http://www.w3.org/2000/svg">
    <defs>
      <radialGradient id="foodTopLeft" cx="0.1" cy="0.1" r="0.9">
        <stop offset="0" stop-color="#e0402a" stop-opacity=".85"/>
        <stop offset=".45" stop-color="#f2d27a" stop-opacity=".55"/>
        <stop offset="1" stop-color="#ffffff" stop-opacity="0"/>
      </radialGradient>
      <radialGradient id="foodTopRight" cx="0.75" cy="0.2" r="0.8">
        <stop offset="0" stop-color="#e4482e" stop-opacity=".7"/>
        <stop offset=".5" stop-color="#a8c98a" stop-opacity=".45"/>
        <stop offset="1" stop-color="#ffffff" stop-opacity="0"/>
      </radialGradient>
      <radialGradient id="avocado" cx="0.6" cy="0.5" r="0.6">
        <stop offset="0" stop-color="#c9d67a" stop-opacity=".9"/>
        <stop offset=".6" stop-color="#5f8c3a" stop-opacity=".6"/>
        <stop offset="1" stop-color="#ffffff" stop-opacity="0"/>
      </radialGradient>
      <linearGradient id="meadow" x1="0" y1="0" x2="0" y2="1">
        <stop offset="0" stop-color="#ffffff" stop-opacity="0"/>
        <stop offset=".45" stop-color="#c9dcb0" stop-opacity=".7"/>
        <stop offset="1" stop-color="#6f9a45"/>
      </linearGradient>
    </defs>

    <rect x="0" y="0" width="330" height="460" fill="url(#foodTopLeft)" role="img" aria-label="Fresh tomatoes, garlic and dry pasta scattered in the top-left corner"/>
    <rect x="600" y="0" width="300" height="220" fill="url(#foodTopRight)" role="img" aria-label="Tomato and basil leaves in the top-right corner"/>
    <rect x="740" y="190" width="160" height="250" fill="url(#avocado)" role="img" aria-label="Halved avocado with seeds and a basil leaf"/>
    <rect x="0" y="500" width="120" height="300" fill="#ffffff" role="img" aria-label="Scattered peppercorns"/>
    <rect x="0" y="880" width="900" height="470" fill="url(#meadow)" role="img" aria-label="Soft green meadow with a splash of milk beneath the pyramid"/>

    <!-- Pyramid -->
    <g class="pyramid">
      <polygon points="448,505 388,636 448,636" fill="var(--apex)"/>
      <polygon points="448,505 508,636 448,636" fill="var(--apex-dark)"/>
      <polygon points="386,642 448,642 448,730 343,730" fill="var(--calories)"/>
      <polygon points="448,642 510,642 552,730 448,730" fill="var(--calories-dark)"/>
      <polygon points="343,736 448,736 448,826 300,826" fill="var(--protein)"/>
      <polygon points="448,736 553,736 596,826 448,826" fill="var(--protein-dark)"/>
      <polygon points="300,832 448,832 448,914 258,914" fill="var(--quality)"/>
      <polygon points="448,832 596,832 638,914 448,914" fill="var(--quality-dark)"/>
      <polygon points="258,920 448,920 448,1004 216,1004" fill="var(--timing)"/>
      <polygon points="448,920 638,920 680,1004 448,1004" fill="var(--timing-dark)"/>
      <polygon points="216,1010 448,1010 448,1094 174,1094" fill="var(--supps)"/>
      <polygon points="448,1010 680,1010 722,1094 448,1094" fill="var(--supps-dark)"/>
      <polygon points="174,1100 448,1100 448,1232 130,1164" fill="var(--noise)"/>
      <polygon points="448,1100 722,1100 768,1164 448,1232" fill="var(--noise-dark)"/>
    </g>

    <!-- Icons -->
    <path class="tier-icon" stroke="none" d="M448,560 c-14,16 -20,28 -14,42 c5,11 23,13 30,2 c6,-10 2,-22 -4,-28 c0,8 -4,12 -7,12 c4,-10 0,-20 -5,-28z"/>
    <g class="tier-icon" stroke="none">
      <ellipse cx="373" cy="785" rx="9" ry="21"/>
      <circle cx="394" cy="778" r="14"/>
      <rect x="388" y="788" width="9" height="16" rx="3"/>
    </g>
    <g class="tier-icon" stroke-width="6" stroke-linecap="round" fill="none">
      <line x1="320" y1="850" x2="358" y2="890"/>
      <line x1="358" y1="850" x2="320" y2="890"/>
    </g>
    <g class="tier-icon" stroke="none">
      <path d="M330,968 h48 a24,16 0 0 1 -48,0z"/>
      <ellipse cx="354" cy="964" rx="18" ry="7"/>
      <rect x="344" y="944" width="3" height="12"/><rect x="352" y="942" width="3" height="14"/><rect x="360" y="944" width="3" height="12"/>
    </g>
    <g class="tier-icon" stroke="none">
      <rect x="334" y="1040" width="9" height="8"/>
      <rect x="328" y="1050" width="34" height="42" rx="4"/>
      <ellipse cx="326" cy="1084" rx="9" ry="6"/>
    </g>
    <g class="tier-icon" stroke="none">
      <rect x="375" y="1170" width="8" height="24"/>
      <polygon points="384,1170 396,1160 396,1204 384,1194"/>
      <rect x="402" y="1166" width="3" height="32"/>
      <rect x="410" y="1172" width="10" height="3"/><rect x="410" y="1181" width="10" height="3"/><rect x="410" y="1190" width="10" height="3"/>
    </g>

    <!-- Labels -->
    <text class="tier-label" x="450" y="697" text-anchor="middle">CALORIES</text>
    <text class="tier-label" x="424" y="792">PROTEIN</text>
    <text class="tier-label" x="382" y="882">FOOD QUALITY</text>
    <text class="tier-label" x="393" y="978">MEAL TIMING</text>
    <text class="tier-label" x="390" y="1085">SUPPLEMENTS</text>
    <text class="tier-label" x="445" y="1191">NOISE</text>
  </svg>

  <h1>
    <span class="title title-the">THE</span>
    <span class="title title-plate">PLATE</span>
    <span class="title title-compass">COMPASS</span>
  </h1>
  <p class="subtitle">Cutting Through the Noise to<br>What Actually Works.</p>

  <div class="author-band"><span class="author-name">AUTHOR NAME</span></div>
</div>
</body>
</html>
```